Flyer for the Radiant Harvest Worship Day

I am looking to create a flyer for a one day prayer retreat our church is organizing.
This flyer will be posted on social media, websites and will also be printed so it can be mailed to people.
I am looking for something professional, with good use of our logo and band colors (logo colors).
I am counting on the designer's skill, creativity, art and knowledge of media communication to produce a flyer that will effectively and quickly convey the message we are trying to spread.
CONTENT OF THE FLYER:
Event title: Radiant Harvest Worship Day
Date: Tuesday July 2nd, 2019
Time: 11:00AM - 7:00PM
Belmora Hotel, 4875 Wexley Avenue, Portland, Maine 04102 (Room: Juniper)
Event Key words to highlight what the event is about: Prayer, Sharing the Word, Panel discussion, prophecy, Impartation.
Key phrases:
A one day prayer retreat.
Jesus Chris is Lord
Contact info:
www.tolvex.org
Phone: 207 555 3184
Email: contact@brookhavenfold.org

```html
<!DOCTYPE html>
<html lang="en">
<head>
<meta charset="utf-8">
<title>Radiant Harvest Worship Day</title>
<link rel="stylesheet" href="https://fonts.googleapis.com/css2?family=Roboto+Condensed:wght@400;700&family=Poppins:wght@600&display=swap">
<style>
  :root {
    --page-bg: #e6e6e6;
    --navy: #0f3458;
    --orange: #f39322;
    --brown: #7a2e17;
    --cream: #fef3dd;
    --peach: #f6deb9;
    --text-navy: #1c3556;
    --white: #ffffff;
  }
  * { margin: 0; padding: 0; box-sizing: border-box; }
  html, body {
    width: 1141px; height: 1200px; overflow: hidden;
    background: var(--page-bg);
  }
  .flyer {
    position: absolute; left: 174px; top: 40px;
    width: 792px; height: 1120px; overflow: hidden;
    font-family: "Roboto Condensed", "Arial Narrow", sans-serif;
  }
  .hero-photo {
    position: absolute; inset: 0;
    background:
      linear-gradient(180deg, rgba(0,0,0,0) 70%, #0b0806 88%),
      radial-gradient(ellipse at 75% 40%, #fff6e2 0%, #f4c27a 28%, #d98a2c 60%, #9a4a16 100%);
  }
  .header {
    position: absolute; left: 34px; top: 37px; width: 758px; height: 166px;
    display: flex;
  }
  .brand {
    width: 165px; background: var(--navy);
    display: flex; align-items: center; justify-content: center;
  }
  .brand-name {
    font-size: 34px; font-weight: 400; color: var(--white); letter-spacing: 1px;
  }
  .title-box {
    flex: 1; background: var(--cream);
    display: flex; flex-direction: column; align-items: center; justify-content: center;
  }
  .event-title {
    font-size: 80px; font-weight: 700; color: var(--orange); line-height: 1;
  }
  .event-subtitle {
    font-size: 25px; font-weight: 700; color: var(--brown); margin-top: 8px;
  }
  .tab { width: 25px; background: var(--orange); }
  .info {
    position: absolute; right: 71px; width: 210px; text-align: right;
  }
  .info-label {
    font-size: 21px; font-weight: 700; color: var(--brown);
    padding-bottom: 6px; border-bottom: 3px solid var(--orange); margin-bottom: 10px;
  }
  .info-text { font-size: 16.5px; color: var(--text-navy); line-height: 1.3; }
  .info-when { top: 242px; }
  .info-where { top: 364px; }
  .keywords {
    position: absolute; right: 71px; top: 538px;
    display: flex; flex-direction: column; align-items: flex-end;
    list-style: none;
  }
  .keywords li {
    font-size: 62px; color: var(--brown); line-height: 76px; height: 76px;
    padding: 0 8px 0 12px;
  }
  .keywords li:nth-child(odd) { background: rgba(254,243,221,0.95); }
  .keywords li:nth-child(even) { background: rgba(246,222,185,0.9); }
  .footer {
    position: absolute; left: 50px; right: 69px; top: 1080px;
    display: flex; justify-content: space-between;
    font-family: "Poppins", Arial, sans-serif; font-weight: 600; font-size: 13.5px;
    color: var(--white);
  }
  .footer .sep { margin: 0 12px; }
</style>
</head>
<body>
  <main class="flyer">
    <div class="hero-photo" role="img" aria-label="Three wooden cross silhouettes on a hill against an orange sunset sky"></div>

    <header class="header">
      <div class="brand"><span class="brand-name">TOLVEX</span></div>
      <div class="title-box">
        <h1 class="event-title">Radiant Harvest</h1>
        <p class="event-subtitle">WORSHIP DAY</p>
      </div>
      <div class="tab"></div>
    </header>

    <section class="info info-when">
      <h2 class="info-label">DATE &amp; TIME</h2>
      <p class="info-text">Tuesday July 2nd, 2019<br>11:00AM - 7:00PM</p>
    </section>

    <section class="info info-where">
      <h2 class="info-label">LOCATION</h2>
      <p class="info-text">Belmora Hotel,<br>4875 Wexley Avenue,<br>Portland, Maine 04102<br>(Room: Juniper)</p>
    </section>

    <ul class="keywords">
      <li>Prayer</li>
      <li>Sharing the Word</li>
      <li>Panel Discussion</li>
      <li>Prophecy</li>
      <li>Impartation</li>
    </ul>

    <footer class="footer">
      <span>Phone: 207 555 3184<span class="sep">|</span>Email: contact@brookhavenfold.org</span>
      <span>www.tolvex.org</span>
    </footer>
  </main>
</body>
</html>
```